Business Card Design - Property Management & Real Estate Services

I need a business card design for my company that I can print ZEPLA Cards. The company is called Brindle Management Company. It is a property management and real estate company. The design has to be clean and modern. I need two versions. One for my employee and one for me. However, the design will be the same, just different text. You can get a feel for the company by looking at our website at www.brindlemanagement.example.

Industry/Entity Type

Property Management

Contact Information for Business Card

I will be using ZEPLA.com to print my cards. I will most likely use the rounded edges card. I need two versions, however, they will be the same design. I need one for me and my employee.

Colors
3276b5
33a6d7

Requirements
Must have
• Company Logo
• Name of person
• Property Management & Real Estate Service
• Phone
• Email
• Website
• Address
• A space to place a QR code

```html
<!DOCTYPE html>
<html lang="en">
<head>
<meta charset="utf-8">
<title>Brindle Management – Business Card</title>
<link rel="stylesheet" href="https://fonts.googleapis.com/css2?family=Roboto:wght@400;500&family=Roboto+Condensed:wght@700&display=swap">
<style>
  :root {
    --backdrop: #c8c8c8;
    --card-blue: #6699cc;
    --brand-deep: #1e4f9c;
    --brand-mid: #3276b5;
    --brand-light: #5a90cc;
    --paper: #f7f7f5;
    --ink: #2b2b2b;
  }
  * { margin: 0; padding: 0; box-sizing: border-box; }
  html, body { width: 1200px; height: 852px; overflow: hidden; }
  body {
    background: var(--backdrop);
    font-family: "Roboto", Arial, sans-serif;
    position: relative;
  }
  .card {
    position: absolute;
    top: 283px;
    width: 500px;
    height: 286px;
    border-radius: 16px;
    overflow: hidden;
  }
  .card--front { left: 70px; background: var(--card-blue); }
  .card--back  { left: 630px; background: var(--paper); }

  .front-brand {
    position: absolute;
    inset: 0;
    display: flex;
    flex-direction: column;
    align-items: center;
    justify-content: center;
    gap: 8px;
    color: var(--brand-deep);
  }
  .front-brand__name {
    font-weight: 500;
    font-size: 34px;
    letter-spacing: 2px;
    text-transform: uppercase;
  }
  .front-brand__tagline {
    font-weight: 500;
    font-size: 12px;
    letter-spacing: 1.5px;
    text-transform: uppercase;
  }
  .qr-space {
    position: absolute;
    right: 22px;
    bottom: 22px;
    width: 56px;
    height: 56px;
    border: 1.5px solid var(--brand-deep);
    border-radius: 4px;
  }

  .back-wordmark {
    position: absolute;
    top: 36px;
    right: 30px;
    font-weight: 500;
    font-size: 24px;
    letter-spacing: 1px;
    color: var(--brand-deep);
    text-transform: uppercase;
  }

  .person {
    position: absolute;
    top: 84px;
    right: 30px;
    text-align: right;
  }
  .person__name {
    font-family: "Roboto Condensed", Arial, sans-serif;
    font-weight: 700;
    font-size: 19px;
    color: var(--brand-deep);
  }
  .person__role {
    font-size: 13px;
    color: var(--ink);
    margin-top: 2px;
  }

  .contacts {
    position: absolute;
    top: 148px;
    right: 30px;
    list-style: none;
    text-align: right;
    font-size: 12px;
    line-height: 19px;
    color: var(--ink);
  }
  .contacts li { display: flex; justify-content: flex-end; align-items: center; gap: 6px; white-space: nowrap; }
  .contacts svg { width: 12px; height: 12px; fill: none; stroke: var(--brand-mid); stroke-width: 1.6; }
  .contacts .no-icon { padding-right: 18px; }

  .building-decoration {
    position: absolute;
    left: 20px;
    bottom: 0;
    width: 170px;
    height: 200px;
    background: linear-gradient(160deg, rgba(90,144,204,0.35), rgba(90,144,204,0.12));
    border-radius: 4px 4px 0 0;
  }
</style>
</head>
<body>
  <section class="card card--front" aria-label="Card front">
    <div class="front-brand">
      <div class="front-brand__name">Brindle Management</div>
      <div class="front-brand__tagline">Property Management &amp; Real Estate Services</div>
    </div>
    <div class="qr-space" aria-label="Space reserved for QR code"></div>
  </section>

  <section class="card card--back" aria-label="Card back">
    <div class="building-decoration" role="img" aria-label="Large line-drawn building decoration in light blue"></div>
    <div class="back-wordmark">Brindle Management</div>
    <div class="person">
      <div class="person__name">Marcos T. Beltrán</div>
      <div class="person__role">Founder</div>
    </div>
    <ul class="contacts">
      <li>(305) 555-0182
        <svg viewBox="0 0 12 12" aria-hidden="true"><path d="M2 1.5h2.5l1 2.5-1.5 1a6 6 0 0 0 3 3l1-1.5 2.5 1V10.5A1 1 0 0 1 9.5 11.5 8.5 8.5 0 0 1 .5 2.5 1 1 0 0 1 2 1.5z"/></svg>
      </li>
      <li>marcos@brindlemanagement.example
        <svg viewBox="0 0 12 12" aria-hidden="true"><rect x="1" y="2.5" width="10" height="7" rx="1"/><path d="M1 3l5 4 5-4"/></svg>
      </li>
      <li>www.brindlemanagement.example
        <svg viewBox="0 0 12 12" aria-hidden="true"><circle cx="6" cy="6" r="5"/><ellipse cx="6" cy="6" rx="2.2" ry="5"/><path d="M1 6h10"/></svg>
      </li>
      <li class="no-icon">480 Harbor Ave #210 Miami, FL 33130</li>
    </ul>
  </section>
</body>
</html>
```